Agrarhandel benötigt Homepage
Zielgruppe
Wir sind ein Agrarhandel mit einem Warenumschlagslager im Sinne eines klassischen Einzelhandels und vertreiben Produkte an Landwirte.
Wir vertreiben folgende Hauptproduktgruppen:
Einzelfuttermittel
wie z.B. Sojaexktraktionsschrot. Die einzelnen Produkte könnten z.B. wie die Futtermittel auf folgender Seite dargestellt werden (https://www.kornprobe-beispiel.eu/de/produkt/trelomixan)
Mischfuttermittel
Hier bieten wir unseren Kunden an, individuelles Mischfutter auf Basis unserer Einzelfuttermittel herzustellen.
Weitere Details und weitere Produktbereiche habe ich in einer Powerpoint-Übersicht dargestellt.
Neben diesen Produkten wollen wir uns als Familienunternehmen selbst vorstellen. Zudem betreiben wir in unserer Familie zusätzlich einen Milchviehbetrieb den wir ebenfalls hervorheben möchten, da wir unseren Kunden gegenüber einerseits als Zulieferer aber auch als Kollege auftreten wollen.
Einzelfuttermittel: Hier können wir durch unsere Unabhängigkeit punkten, da wir nicht abhängig von bestimmten Lieferanten sind und dementsprechend unabhängig beraten können. Wir untersuchen im Vergleich zu unseren Wettbewerben die Qualität der Futtermittel bis ins Detail und können daher eine Transparenz bieten, die Konkurrenten in der Regel nicht bieten können. Unser Warenumschlagsplatz mit moderner Technik ermöglicht es uns äußerst kosteneffizient die Waren umschlagen und ausliefern zu können.
Mischfuttermittel: Auf Basis der vorhandenen Einzelfuttermittel stellen wir je nach Kundenwunsch individuelle Mischfutter her. Wir arbeiten mit offenen Deklarationen, sodass unsere Kunden jederzeit nachvollziehen können, ob auch die Einzelfuttermittel verwendet wurden, die sie bestellt haben und keine billigen Ersatzprodukte verwendet wurden.
Zudem sind wir BT und HUPA zertifiziert. Die aktuellen für unser Unternehmen ausgestellten Zertifikate müssen für unsere Kunden als Download zur Verfügung stehen. Statt dem HUPA-Logo bitte das ..
Aufgabenstellung
Wir möchten gerne ein zeitgemäße Homepage, jedoch muss auch berücksichtigt werden, dass unsere Kunden eher konservativ denken.

```html
<!DOCTYPE html>
<html lang="de">
<head>
<meta charset="utf-8">
<title>Altmühl Landhandel – Qualitativ hochwertiges Futter</title>
<link href="https://fonts.googleapis.com/css2?family=Fira+Sans:wght@400;500;600;700&family=Open+Sans:ital,wght@0,400;0,600;0,700;1,400&display=swap" rel="stylesheet">
<style>
:root{
  --green:#1d6a48;
  --green-dark:#155a3c;
  --yellow:#f5b50a;
  --text:#333;
  --grey-bg:#efefef;
  --bar-grey:#d9d9d9;
  --white:#fff;
}
*{box-sizing:border-box;margin:0;padding:0}
html,body{width:1200px;height:3656px;overflow:hidden;background:var(--white)}
body{position:relative;font-family:"Open Sans",sans-serif;color:var(--text)}
.abs{position:absolute}
.heading{font-family:"Fira Sans",sans-serif;font-weight:600;color:var(--green);text-transform:uppercase;letter-spacing:.5px}

/* top bar */
.topbar{left:0;top:0;width:1200px;height:37px;background:var(--green)}
.topbar-cta{left:773px;top:10px;font-size:13px;color:#fff}
.topbar-phone{left:984px;top:8px}
.topbar-num{left:1014px;top:10px;font-size:13px;color:#fff}

/* header */
.header{left:0;top:37px;width:1200px;height:101px;background:#fff}
.nav a{position:absolute;top:88px;font-size:12.5px;font-weight:600;color:#333;text-decoration:none;letter-spacing:.3px}
.burger{left:1072px;top:88px;width:27px}
.burger span{display:block;height:3px;background:#333;margin-bottom:4px}
.brand-disc{left:504px;top:24px;width:192px;height:192px;border-radius:50%;background:#fff;z-index:3;display:flex;align-items:center;justify-content:center;text-align:center}
.brand-disc span{font-family:"Fira Sans",sans-serif;font-weight:600;color:var(--green);font-size:16px;line-height:1.2;margin-top:-50px}

/* hero */
.hero{left:0;top:138px;width:1200px;height:550px;background:linear-gradient(100deg,#3b3a22 0%,#6b5a2c 35%,#9b8a4a 60%,#c9b46a 80%,#8a9a3e 100%)}
.hero-shade{left:0;top:138px;width:1200px;height:550px;background:linear-gradient(90deg,rgba(0,0,0,.35),rgba(0,0,0,0) 55%)}
.hero-title{left:100px;top:312px;font-family:"Fira Sans",sans-serif;font-weight:700;font-size:43px;color:#fff;letter-spacing:1px}
.hero-sub{left:100px;top:382px;font-family:"Fira Sans",sans-serif;font-size:28px;line-height:45px;color:#fff}
.btn-yellow{background:var(--yellow);color:#333;font-weight:700;font-size:14px;border-radius:9px;display:flex;align-items:center;justify-content:center;letter-spacing:.3px}
.hero-btn{left:100px;top:496px;width:246px;height:37px}
.dots{left:575px;top:640px;display:flex;gap:8px}
.dots i{width:11px;height:11px;border-radius:50%;background:rgba(255,255,255,.5);display:block}
.dots i:first-child{background:#fff}

/* about */
.photo-a{left:100px;top:758px;width:292px;height:292px;background:linear-gradient(160deg,#4a4036,#8a7a66 50%,#b59a6a)}
.photo-b{left:227px;top:882px;width:296px;height:300px;background:linear-gradient(170deg,#5a4a3a,#8d7458 45%,#b38a56 75%,#8a6440);border:6px solid #fff;border-right:0;border-bottom:0}
.badge{left:342px;top:836px;width:100px;height:100px;border-radius:50%;background:var(--green);border:4px solid #fff;display:flex;align-items:center;justify-content:center}
.about-title{left:553px;top:750px;font-size:42px;line-height:56px}
.about-text{left:553px;top:874px;width:545px;font-size:13.6px;line-height:18.3px;color:#333}
.about-text p{margin-bottom:18px}
.phone-btn{left:552px;top:1130px;width:241px;height:47px;background:var(--green);border-radius:8px;color:#fff;font-size:20px;display:flex;align-items:center;padding-left:20px;gap:16px}

/* features */
.features{left:0;top:1255px;width:1200px;height:439px;background:var(--grey-bg)}
.hands{left:400px;top:1255px;width:410px;height:320px;background:radial-gradient(ellipse at 50% 60%,#8a5a3a 0%,#b47c58 30%,#d9a88a 55%,rgba(239,239,239,0) 72%)}
.feature{position:absolute;width:300px;text-align:center}
.feature svg{display:block;margin:0 auto 6px}
.feature h3{font-family:"Fira Sans",sans-serif;font-weight:600;font-size:21px;color:#333;letter-spacing:.4px}
.feature p{font-size:13px;line-height:18px;color:#555;margin-top:4px}

/* products */
.products-title{left:0;width:1200px;top:1755px;text-align:center;font-size:40px}
.cat{position:absolute;top:1840px;width:160px;text-align:center}
.cat .ic{width:68px;height:68px;border-radius:50%;background:#ddd;margin:0 auto 10px;display:flex;align-items:center;justify-content:center}
.cat.active .ic{background:var(--green)}
.cat span{font-size:16.5px;color:#333}
.card{position:absolute;top:1985px;width:246px;height:418px;border:1px solid #ddd;border-radius:6px;background:#fff;padding:0 15px}
.pile{margin:20px auto 0;width:170px;height:50px;border-radius:50% 50% 8% 8%/100% 100% 10% 10%}
.card h4{font-family:"Fira Sans",sans-serif;font-weight:500;font-size:22px;text-align:center;color:#333;margin:12px 0 8px;text-transform:uppercase}
.row{height:35px}
.row .lab{font-size:11px;color:#333;display:block}
.bar{height:4px;margin-top:6px;background:repeating-linear-gradient(90deg,var(--bar-grey) 0 7px,transparent 7px 9px);position:relative}
.bar b{position:absolute;left:0;top:0;height:4px;background:repeating-linear-gradient(90deg,var(--green) 0 7px,transparent 7px 9px)}
.bar.gold b{background:repeating-linear-gradient(90deg,var(--yellow) 0 7px,transparent 7px 9px)}
.more{font-size:11px;color:#bbb;text-align:center;margin-top:2px}
.arrow{top:2180px}

/* newsletter */
.news{left:0;top:2507px;width:1200px;height:400px;background:linear-gradient(90deg,#4a3a2a 0%,#7a6448 40%,#a08a6a 65%,#6a5a4a 100%)}
.news-shade{left:0;top:2507px;width:1200px;height:400px;background:rgba(0,0,0,.25)}
.mail{left:560px;top:2467px;width:80px;height:80px;border-radius:50%;background:var(--yellow);display:flex;align-items:center;justify-content:center;z-index:2}
.news-title{left:100px;top:2604px;font-family:"Fira Sans",sans-serif;font-weight:600;font-size:40px;line-height:57px;color:#fff;letter-spacing:1px}
.field{position:absolute;left:703px;width:396px;height:35px;background:rgba(255,255,255,.82);border-radius:6px;font-size:14px;color:#888;padding:8px 18px}
.check{left:703px;top:2800px;font-size:13px;color:#fff;display:flex;gap:8px;align-items:center}
.check i{width:16px;height:16px;background:rgba(255,255,255,.8);border-radius:3px;display:block}
.send{left:703px;top:2842px;width:195px;height:37px}

/* partners */
.partner{position:absolute;font-family:"Open Sans",sans-serif;font-weight:700;color:#777;font-size:24px;display:flex;align-items:center;gap:10px}
.partner i{width:30px;height:30px;border-radius:50%;background:#999;display:block}

/* footer */
.footer{left:0;top:3199px;width:1200px;height:342px;background:linear-gradient(90deg,#145a3c,#1d6a48 60%,#237a54)}
.vline{top:3199px;width:1px;height:342px;background:rgba(255,255,255,.5)}
.f-name{left:0;width:494px;top:3340px;text-align:center;font-family:"Fira Sans",sans-serif;font-weight:500;font-size:19px;color:#fff}
.f-brand{left:205px;top:3250px;width:80px;height:80px;border-radius:50%;border:2px solid #fff}
.f-addr{left:0;width:494px;top:3390px;text-align:center;font-size:13px;line-height:18px;color:#fff}
.f-contact{font-size:13px;color:#fff;display:flex;align-items:center;gap:10px}
.f-contact i{width:17px;height:17px;border-radius:50%;background:var(--yellow);display:block}
.f-title{top:3250px;font-size:14px;font-weight:700;color:#fff;text-align:center;letter-spacing:.4px}
.f-links{left:494px;width:211px;top:3336px;text-align:center;font-size:13.5px;line-height:18px;color:#fff}
.f-about{left:805px;width:300px;top:3318px;text-align:center;font-size:12px;line-height:18.5px;font-style:italic;color:#fff}
.copy{left:0;top:3541px;width:1200px;height:42px;background:#111;color:#fff;font-size:13px;text-align:center;line-height:42px}
</style>
</head>
<body>

<!-- top bar -->
<div class="abs topbar"></div>
<div class="abs topbar-cta">Jetzt telefonisch beraten lassen</div>
<svg class="abs topbar-phone" width="20" height="20" viewBox="0 0 20 20"><circle cx="10" cy="10" r="10" fill="#f5b50a"/><path d="M7 5.5l1.5 2.5-1 1.2a7 7 0 003.3 3.3l1.2-1 2.5 1.5-.7 1.8c-4 .3-8.6-4.3-8.3-8.3z" fill="#fff"/></svg>
<div class="abs topbar-num">09123 456780</div>

<!-- header -->
<div class="abs header"></div>
<nav class="nav">
  <a style="left:100px">EINZELFUTTERMITTEL</a>
  <a style="left:284px">MISCHFUTTERMITTEL</a>
  <a style="left:725px">ÜBER UNS</a>
  <a style="left:831px">UNSER BETRIEB</a>
  <a style="left:970px">KONTAKT</a>
</nav>
<div class="abs burger"><span></span><span></span><span></span></div>

<!-- hero -->
<div class="abs hero" role="img" aria-label="Kuh auf einer Weide im Abendlicht, weitere Rinder im Hintergrund"></div>
<div class="abs hero-shade"></div>
<div class="abs brand-disc"><span>Altmühl<br>Landhandel</span></div>
<h1 class="abs hero-title">ALTMÜHL LANDHANDEL</h1>
<p class="abs hero-sub">Qualitativ hochwertiges Futter<br>für beste Tiergesundheit</p>
<div class="abs btn-yellow hero-btn">JETZT BERATEN LASSEN</div>
<div class="abs dots"><i></i><i></i><i></i></div>

<!-- about -->
<div class="abs photo-a" role="img" aria-label="Kühe im Stall beim Fressen am Futtertisch"></div>
<div class="abs photo-b" role="img" aria-label="Kälber an Futterkübeln mit Getreide im Stall"></div>
<div class="abs badge">
  <svg width="52" height="52" viewBox="0 0 52 52" fill="none" stroke="#fff" stroke-width="2.5" stroke-linecap="round"><circle cx="26" cy="26" r="22"/><path d="M26 38V22M26 30c-7 0-11-5-11-11 7 0 11 4 11 11zM26 26c0-7 4-11 11-11 0 6-4 11-11 11z"/></svg>
</div>
<h2 class="abs heading about-title">Das Tierwohl ist<br>unsere Priorität</h2>
<div class="abs about-text">
  <p>Wir von Altmühl Landhandel sind ein Familienunternehmen für Einzel- und Mischfutter. Unsere jahrelange Erfahrung durch unseren eigenen Milchviehbetrieb zeigt uns, wie wichtig hochwertige Nahrung für den optimalen Energie- und Nährstoffbedarf ist. Dieses Wissen wollen wir an unsere Kunden weitergeben.</p>
  <p>Unsere Unabhängigkeit erlaubt uns Sie individuell zu beraten und gemeinsam mit Ihnen das perfekte Futter für Ihre Tiere und deren Bedürfnisse zu finden, egal ob Einzel- oder Mischfutter. Alle Futtermittel werden von uns bis ins kleinste Detail auf ihre Qualität überprüft. Modernste Technik ermöglicht es uns äußerst kosteneffizient die Waren umschlagen und ausliefern zu können, europaweit.</p>
  <p>Gemeinsam für mehr Tierwohl in der Nutztierhaltung. Lassen Sie sich von uns gerne telefonisch oder per WhatsApp beraten.</p>
</div>
<div class="abs phone-btn">
  <svg width="28" height="28" viewBox="0 0 20 20"><circle cx="10" cy="10" r="10" fill="#f5b50a"/><path d="M7 5.5l1.5 2.5-1 1.2a7 7 0 003.3 3.3l1.2-1 2.5 1.5-.7 1.8c-4 .3-8.6-4.3-8.3-8.3z" fill="#fff"/></svg>
  09123 45 67 80
</div>

<!-- features -->
<div class="abs features"></div>
<div class="abs hands" role="img" aria-label="Zwei Hände halten eine Handvoll Futterkörner"></div>
<div class="feature" style="left:126px;top:1295px">
  <svg width="70" height="70" viewBox="0 0 70 70" fill="none" stroke="#1d6a48" stroke-width="2.2" stroke-linecap="round" stroke-linejoin="round"><path d="M8 52h12l10 4h14l16-10-3-4-14 6H30M20 46h14a4 4 0 010 8"/><path d="M40 40V24M40 32c-8 0-12-5-12-12 8 0 12 5 12 12zM40 28c0-8 5-14 14-14 0 8-5 14-14 14z"/></svg>
  <h3>TRANSPARENT</h3>
  <p>Wir untersuchen die<br>Qualität der Futtermittel<br>bis ins Detail</p>
</div>
<div class="feature" style="left:779px;top:1295px">
  <svg width="70" height="70" viewBox="0 0 70 70" fill="none" stroke="#1d6a48" stroke-width="2.2" stroke-linecap="round" stroke-linejoin="round"><path d="M35 6l7 5 9-1 3 8 8 4-2 9 4 8-7 5-1 9-9 1-5 7-7-4-8 3-4-8-8-3 1-9-5-7 6-6-1-9 9-2 4-8 8 3z"/><circle cx="35" cy="35" r="16"/><path d="M27 35l6 6 10-12"/></svg>
  <h3>ZERTIFIZIERT</h3>
  <p>Wir sind BT und<br>HUPA zertifiziert</p>
</div>
<div class="feature" style="left:173px;top:1487px">
  <svg width="70" height="70" viewBox="0 0 70 70" fill="none" stroke="#1d6a48" stroke-width="2.2" stroke-linecap="round" stroke-linejoin="round"><circle cx="38" cy="38" r="22"/><path d="M32 10h12M38 10v6M52 20l4-4"/><circle cx="22" cy="50" r="12" fill="#efefef"/><path d="M16 50l4 4 8-8M38 38l10-10"/></svg>
  <h3>KOSTENEFFIZIENT</h3>
  <p>Kosteneffizientes Umschlagen<br>und Ausliefern der Ware durch<br>modernste Technik</p>
</div>
<div class="feature" style="left:726px;top:1487px">
  <svg width="70" height="70" viewBox="0 0 70 70" fill="none" stroke="#1d6a48" stroke-width="2.2" stroke-linejoin="round"><path d="M10 10h20v7a5 5 0 010 8v7H22a5 5 0 00-8 0h-4z"/><path d="M34 36h22v22H34v-8a5 5 0 000-8z"/><path d="M12 36h18v8a5 5 0 010 6v8H12z"/><path d="M36 14h16v18H36"/></svg>
  <h3>INDIVIDUELL</h3>
  <p>Auf Basis der vorhandenen Einzelfutter-<br>mittel stellen wir, je nach Ihren Wünschen,<br>individuelles Mischfutter her</p>
</div>

<!-- products -->
<h2 class="abs heading products-title">Unsere Produkte</h2>
<div class="cat active" style="left:192px"><div class="ic"><svg width="36" height="36" viewBox="0 0 36 36" fill="none" stroke="#f5b50a" stroke-width="2" stroke-linecap="round"><path d="M6 30L28 8M12 22c-3-4-2-8 2-10 2 4 1 8-2 10zM18 16c-3-4-2-8 2-10 2 4 1 8-2 10zM14 24c4 3 8 2 10-2-4-2-8-1-10 2zM20 18c4 3 8 2 10-2-4-2-8-1-10 2z"/></svg></div><span>Einzelfuttermittel</span></div>
<div class="cat" style="left:377px"><div class="ic"><svg width="34" height="34" viewBox="0 0 34 34" fill="none" stroke="#1d6a48" stroke-width="2"><path d="M8 5h18l2 6v18H6V11z"/><circle cx="17" cy="19" r="5"/></svg></div><span>Mischfuttermittel</span></div>
<div class="cat" style="left:567px"><div class="ic"><svg width="34" height="34" viewBox="0 0 34 34" fill="none" stroke="#1d6a48" stroke-width="2"><path d="M8 5h18l2 6v18H6V11z"/><path d="M17 13c-3 4-4 6-4 8a4 4 0 008 0c0-2-1-4-4-8z"/></svg></div><span>Flüssigfuttermittel</span></div>
<div class="cat" style="left:741px"><div class="ic"><svg width="34" height="34" viewBox="0 0 34 34" fill="none" stroke="#1d6a48" stroke-width="2"><path d="M8 5h18l2 6v18H6V11z"/><rect x="11" y="14" width="12" height="10"/></svg></div><span>Mineralfutter</span></div>
<div class="cat" style="left:881px"><div class="ic"><svg width="34" height="34" viewBox="0 0 34 34" fill="none" stroke="#1d6a48" stroke-width="2" stroke-linecap="round"><path d="M7 27L27 7M7 7l20 20M24 5l5 5M5 24l5 5"/></svg></div><span>Sonstiges</span></div>

<svg class="abs arrow" style="left:70px" width="16" height="26" viewBox="0 0 16 26" fill="none" stroke="#999" stroke-width="2"><path d="M13 3L3 13l10 10"/></svg>
<svg class="abs arrow" style="left:1111px" width="16" height="26" viewBox="0 0 16 26" fill="none" stroke="#999" stroke-width="2"><path d="M3 3l10 10L3 23"/></svg>

<div class="card" style="left:100px">
  <div class="pile" role="img" aria-label="Haufen Weizenpellets" style="background:linear-gradient(#a49a80,#7a705a)"></div>
  <h4>Duo Plus Weizen</h4>
  <div class="row"><span class="lab">12,4% Feuchtigkeitsgehalt</span><div class="bar"><b style="width:10%"></b></div></div>
  <div class="row"><span class="lab">45,2% Rohprotein</span><div class="bar"><b style="width:50%"></b></div></div>
  <div class="row"><span class="lab">2.1% Rohfett</span><div class="bar"><b style="width:5%"></b></div></div>
  <div class="row"><span class="lab">12.2% Rohfaser</span><div class="bar"><b style="width:10%"></b></div></div>
  <div class="row"><span class="lab">5.0% Stärke</span><div class="bar"><b style="width:5%"></b></div></div>
  <div class="row"><span class="lab">10.0% Zucker</span><div class="bar"><b style="width:10%"></b></div></div>
  <div class="row"><span class="lab">75.0% Eiweiß</span><div class="bar gold"><b style="width:74%"></b></div></div>
  <div class="more">Produkte anzeigen ›</div>
</div>
<div class="card" style="left:352px">
  <div class="pile" role="img" aria-label="Haufen Rapsschrot" style="background:linear-gradient(#8a5a2a,#5a3412)"></div>
  <h4>Trelorap</h4>
  <div class="row"><span class="lab">12,4% Feuchtigkeitsgehalt</span><div class="bar"><b style="width:10%"></b></div></div>
  <div class="row"><span class="lab">45,2% Rohprotein</span><div class="bar"><b style="width:50%"></b></div></div>
  <div class="row"><span class="lab">2.1% Rohfett</span><div class="bar"><b style="width:5%"></b></div></div>
  <div class="row"><span class="lab">12.2% Rohfaser</span><div class="bar"><b style="width:10%"></b></div></div>
  <div class="row"><span class="lab">5.0% Stärke</span><div class="bar"><b style="width:5%"></b></div></div>
  <div class="row"><span class="lab">10.0% Zucker</span><div class="bar"><b style="width:10%"></b></div></div>
  <div class="row"><span class="lab">75.0% Eiweiß</span><div class="bar gold"><b style="width:74%"></b></div></div>
  <div class="more">Produkte anzeigen ›</div>
</div>
<div class="card" style="left:603px">
  <div class="pile" role="img" aria-label="Haufen Sojaschrot" style="background:linear-gradient(#d9b880,#a88450)"></div>
  <h4>Treloso</h4>
  <div class="row"><span class="lab">12,4% Feuchtigkeitsgehalt</span><div class="bar"><b style="width:10%"></b></div></div>
  <div class="row"><span class="lab">45,2% Rohprotein</span><div class="bar"><b style="width:50%"></b></div></div>
  <div class="row"><span class="lab">2.1% Rohfett</span><div class="bar"><b style="width:5%"></b></div></div>
  <div class="row"><span class="lab">12.2% Rohfaser</span><div class="bar"><b style="width:10%"></b></div></div>
  <div class="row"><span class="lab">5.0% Stärke</span><div class="bar"><b style="width:5%"></b></div></div>
  <div class="row"><span class="lab">10.0% Zucker</span><div class="bar"><b style="width:10%"></b></div></div>
  <div class="row"><span class="lab">75.0% Eiweiß</span><div class="bar gold"><b style="width:74%"></b></div></div>
  <div class="more">Produkte anzeigen ›</div>
</div>
<div class="card" style="left:852px">
  <div class="pile" role="img" aria-label="Haufen Lupinenschrot" style="background:linear-gradient(#e0b050,#a87a30)"></div>
  <h4>Trelolup</h4>
  <div class="row"><span class="lab">12,4% Feuchtigkeitsgehalt</span><div class="bar"><b style="width:10%"></b></div></div>
  <div class="row"><span class="lab">45,2% Rohprotein</span><div class="bar"><b style="width:50%"></b></div></div>
  <div class="row"><span class="lab">2.1% Rohfett</span><div class="bar"><b style="width:5%"></b></div></div>
  <div class="row"><span class="lab">12.2% Rohfaser</span><div class="bar"><b style="width:10%"></b></div></div>
  <div class="row"><span class="lab">5.0% Stärke</span><div class="bar"><b style="width:5%"></b></div></div>
  <div class="row"><span class="lab">10.0% Zucker</span><div class="bar"><b style="width:10%"></b></div></div>
  <div class="row"><span class="lab">75.0% Eiweiß</span><div class="bar gold"><b style="width:74%"></b></div></div>
  <div class="more">Produkte anzeigen ›</div>
</div>

<!-- newsletter -->
<div class="abs news" role="img" aria-label="Schale mit Futtermischung im Stall, Kühe im Hintergrund"></div>
<div class="abs news-shade"></div>
<div class="abs mail"><svg width="44" height="32" viewBox="0 0 44 32" fill="none" stroke="#fff" stroke-width="2.5" stroke-linejoin="round"><rect x="2" y="2" width="40" height="28" rx="2"/><path d="M2 3l20 16L42 3M2 29l15-13M42 29L27 16"/></svg></div>
<h2 class="abs news-title">BLEIBEN SIE ÜBER<br>UNSERE PRODUKTE<br>INFORMIERT</h2>
<div class="field" style="top:2577px">Name</div>
<div class="field" style="top:2630px">Anschrift</div>
<div class="field" style="top:2689px">E-Mail Adresse</div>
<div class="field" style="top:2747px">Betriebsnummer</div>
<div class="abs check"><i></i>Ich habe die Datenschutzerklärung gelesen und akzeptiert.</div>
<div class="abs btn-yellow send">ANMELDEN</div>

<!-- partners -->
<div class="partner" style="left:100px;top:2985px"><i></i>Halm</div>
<div class="partner" style="left:295px;top:2985px"><i></i>Kornprobe</div>
<div class="partner" style="left:665px;top:2985px"><i></i>Basalt</div>
<div class="partner" style="left:960px;top:2990px">Saatwerk</div>
<div class="partner" style="left:190px;top:3090px">Kalbvita</div>
<div class="partner" style="left:452px;top:3090px;font-size:19px">Nordhafen Leistungsfutter</div>
<div class="partner" style="left:752px;top:3090px;font-size:21px">Ackerfeld Saaten</div>

<!-- footer -->
<div class="abs footer"></div>
<div class="abs vline" style="left:494px"></div>
<div class="abs vline" style="left:705px"></div>
<div class="abs f-brand"></div>
<div class="abs f-name">ALTMÜHL LANDHANDEL</div>
<div class="abs f-addr">Feldweg 4<br>91234 Musterbach</div>
<div class="abs f-contact" style="left:110px;top:3451px"><i></i>09123 45 67 80</div>
<div class="abs f-contact" style="left:250px;top:3451px"><i></i>info@altmuehl-landhandel.de</div>
<div class="abs f-contact" style="left:110px;top:3478px"><i></i>0171 234 56 78</div>
<div class="abs f-contact" style="left:250px;top:3478px"><i></i>www.altmuehl-landhandel.de</div>
<div class="abs f-title" style="left:494px;width:211px">INFORMATIONEN</div>
<div class="abs f-links">AGB<br>Datenschutz<br>Kontakt<br>Impressum<br>Sitemap</div>
<div class="abs f-title" style="left:705px;width:495px">ÜBER UNS</div>
<div class="abs f-about">Wir von Altmühl Landhandel sind ein Familienunterne-hmen für Einzel- und Mischfutter. Unsere jahrelange Erfahrung durch unseren eigenen Milchviehbetrieb zeigt uns, wie wichtig hochwertige Nahrung für das Tierwohlbefinden ist. Dieses Wissen wollen wir an unsere Kunden weitergeben.</div>
<div class="abs copy">©2023 Altmühl Landhandel</div>

</body>
</html>
```